Looking for a cool & simple business-card-design for digital agency

Hi!

We are a web agency that offers Reputation Management, Vextor & Seo Services and software development. We like cool things, we like innovative styles.

We have uploaded our logo.

Project Deadline Extended Reason: Client does not want any designs with the colorful logo. Please send us submissions ONLY with the blac and white logo. What the client would like to see:1) Back of the card: is a silver logo on a black background2) front of the card with all the data, please use white background and black logo thank you Added Friday, May 8, 2015

Industry/Entity Type

Software

```html
<!DOCTYPE html>
<html lang="en">
<head>
<meta charset="utf-8">
<title>Nordlicht AG – Business Card</title>
<link rel="stylesheet" href="https://fonts.googleapis.com/css2?family=Open+Sans:wght@300;400;700&display=swap">
<style>
  :root {
    --stage: #e9e7e3;
    --card-white: #fbfbfb;
    --card-black: #0d0d0d;
    --ink: #2b2b2b;
    --ink-soft: #555;
    --silver: #cfcfcf;
    --silver-soft: #9a9a9a;
    --rule: #8a8a8a;
  }
  * { margin: 0; padding: 0; box-sizing: border-box; }
  html, body { width: 1200px; height: 1023px; overflow: hidden; }
  body {
    background: var(--stage);
    font-family: "Open Sans", Arial, sans-serif;
    position: relative;
  }
  .card {
    position: absolute;
    width: 560px;
    height: 320px;
    border-radius: 24px;
    box-shadow: 0 10px 30px rgba(0,0,0,0.18);
    overflow: hidden;
  }
  .card--front { left: 90px; top: 150px; background: var(--card-white); color: var(--ink); }
  .card--back {
    left: 550px; top: 550px;
    background: radial-gradient(ellipse at 30% 30%, #2a2a2a 0%, var(--card-black) 65%);
  }
  .brand { position: absolute; display: flex; align-items: center; gap: 14px; }
  .brand__mark { width: 26px; height: 26px; }
  .brand__text { display: flex; flex-direction: column; border-left: 1px solid var(--rule); padding-left: 12px; }
  .brand__name { font-weight: 700; font-size: 34px; line-height: 1; letter-spacing: 0.5px; }
  .brand__tagline { font-weight: 300; font-size: 15px; letter-spacing: 5px; margin-top: 4px; }
  .card--front .brand { left: 40px; top: 40px; }
  .card--front .brand__mark { background: var(--ink); }
  .card--front .brand__tagline { color: var(--ink-soft); }
  .card--back .brand { left: 60px; top: 120px; }
  .card--back .brand__mark { background: var(--silver-soft); }
  .card--back .brand__name { color: var(--silver); font-size: 40px; }
  .card--back .brand__tagline { color: var(--silver-soft); font-size: 17px; }
  .person { position: absolute; left: 40px; top: 150px; }
  .person__name { font-weight: 700; font-size: 17px; }
  .person__role { font-weight: 400; font-size: 14px; color: var(--ink-soft); }
  .contacts { position: absolute; left: 220px; top: 150px; list-style: none; font-size: 14px; line-height: 24px; }
  .contacts li { display: flex; align-items: center; gap: 10px; }
  .contacts svg { width: 13px; height: 13px; fill: none; stroke: var(--ink); stroke-width: 1.6; }
</style>
</head>
<body>
  <section class="card card--front" aria-label="Card front">
    <div class="brand">
      <span class="brand__mark"></span>
      <div class="brand__text">
        <span class="brand__name">Nordlicht AG</span>
        <span class="brand__tagline">DIGITALE STRATEGIEN</span>
      </div>
    </div>
    <div class="person">
      <p class="person__name">Lena Marsh</p>
      <p class="person__role">Director</p>
    </div>
    <ul class="contacts">
      <li><svg viewBox="0 0 14 14"><path d="M3 1h3l1 3-2 1a7 7 0 0 0 4 4l1-2 3 1v3a1 1 0 0 1-1 1A11 11 0 0 1 2 2a1 1 0 0 1 1-1z"/></svg>000 555 6120</li>
      <li><svg viewBox="0 0 14 14"><rect x="3" y="1" width="8" height="12" rx="1"/></svg>333 7781 904</li>
      <li><svg viewBox="0 0 14 14"><rect x="1" y="3" width="12" height="8"/><path d="M1 3l6 5 6-5"/></svg>info@nordlichtag.com</li>
      <li><svg viewBox="0 0 14 14"><circle cx="7" cy="7" r="6"/><path d="M1 7h12M7 1c3 3 3 9 0 12M7 1c-3 3-3 9 0 12"/></svg>www.nordlichtag.com</li>
    </ul>
  </section>

  <section class="card card--back" aria-label="Card back">
    <div class="brand">
      <span class="brand__mark"></span>
      <div class="brand__text">
        <span class="brand__name">Nordlicht AG</span>
        <span class="brand__tagline">DIGITALE STRATEGIEN</span>
      </div>
    </div>
  </section>
</body>
</html>
```